Equipment Finance Specialist I work with companies who need the funds to buy their equipment

I would like a business card that stands out on the shelves. I want to be able to hand it to someone and say WOW. This card should have my logo.
You can put color into it I am very open on design and color

What my company does is we deal with dealerships that sell equipment such as Dump Trucks garbage trucks tractors trailers. Customers get referred to us and depending on their time in business we will ask for the following items

Companies that have been in business for more than two years we have a credit application program up to 250K . With this program we need the following items Credit application filled out(which is what I would like to be able for the customer to click on my website to get.) as well as three current month bank statements.

Deals over 250k we will need the following items

2 years business tax returns
2 years personal tax returns
Profit & Loss statement
Personal Financial Statement

what we do
100% FINANCING
SEASONAL PAYMENTS
LOAN BALLOON PAYMENTS
TRAC LEASING
LOW-INTEREST REFINANCING RATES
DEBT CONSOLIDATION

We specialize in creative financing solutions and offer a variety of reliable, flexible and expandable lending choices.

Target Market(s)

Trucking Companies

Industry/Entity Type

Trucking Company

Contact Information for Business Card

* $250,000 Application only Program
* Loans from $30,000 to 5,000,000
* Competitive Interest Rates

Font styles to use
Serif
Sans Serif

Colors

Designer to choose colors to be used in the design.

Requirements
Must have
• On the back of the card.
• * $250,000 Application only Program
• * Loans from $30,000 to 5,000,000
• My name, email, website. address
• * Competitive Interest Rates
• * 100% Financing
Nice to have
• I want my logo to pop on the card
• My logo is the great one I would like to use
Should not have
• I am up for your creativity as well

```html
<!DOCTYPE html>
<html lang="en">
<head>
<meta charset="utf-8">
<title>Ridgeline Financing – Business Card</title>
<link href="https://fonts.googleapis.com/css2?family=Montserrat:wght@800&family=Open+Sans:wght@400;600&display=swap" rel="stylesheet">
<style>
  :root {
    --bg: #2a2a2b;
    --card: #58585a;
    --ink-dark: #1c1c1e;
    --ink-light: #e4e4e6;
    --brand-blue: #1f2f78;
    --brand-red: #e11d2e;
  }
  * { margin: 0; padding: 0; box-sizing: border-box; }
  html, body { width: 1200px; height: 895px; overflow: hidden; background: var(--bg); }
  body { position: relative; font-family: "Open Sans", sans-serif; color: var(--ink-light); }

  .card {
    position: absolute;
    width: 540px; height: 309px;
    background: var(--card);
    border-radius: 18px;
    overflow: hidden;
    box-shadow: 0 18px 40px rgba(0,0,0,.45);
  }
  .card--back  { left: 40px;  top: 293px; }
  .card--front { left: 620px; top: 293px; }

  /* wordmark */
  .wordmark {
    position: absolute;
    display: flex; align-items: center; gap: 12px;
    font-family: "Montserrat", sans-serif; font-weight: 800;
    letter-spacing: 1px; line-height: 1;
  }
  .wordmark__dot { width: 22px; height: 22px; border-radius: 50%; flex: none; }
  .card--back .wordmark { left: 0; right: 0; top: 92px; justify-content: center; font-size: 34px; color: var(--ink-dark); }
  .card--back .wordmark__dot { background: var(--ink-dark); }
  .card--front .wordmark { left: 150px; top: 128px; font-size: 28px; color: var(--brand-blue); }
  .card--front .wordmark__dot { background: var(--brand-blue); }

  /* back side: programs */
  .programs { position: absolute; left: 0; right: 0; top: 190px; text-align: center; font-size: 15px; line-height: 1.75; }
  .programs__sep { display: inline-block; width: 7px; height: 7px; border-radius: 50%; background: var(--ink-light); margin: 0 10px; vertical-align: middle; }

  /* front side */
  .holder { position: absolute; left: 0; top: 30px; padding-left: 34px; }
  .holder::before { content: ""; position: absolute; left: 0; top: 4px; width: 14px; height: 40px; background: var(--brand-red); }
  .holder__name { font-family: "Montserrat", sans-serif; font-weight: 800; font-size: 24px; color: var(--brand-blue); letter-spacing: .5px; }
  .holder__role { font-size: 15px; color: var(--ink-light); }

  .address { position: absolute; right: 30px; top: 186px; text-align: left; font-size: 13px; line-height: 1.45; }

  .contact { position: absolute; left: 30px; bottom: 34px; list-style: none; font-size: 14px; line-height: 1.6; }
  .contact li { display: flex; align-items: center; gap: 10px; }
  .contact svg { width: 14px; height: 14px; fill: var(--brand-red); flex: none; }

  .edge { position: absolute; left: 0; right: 0; bottom: 0; height: 8px; display: flex; }
  .edge__blue { flex: 6; background: var(--brand-blue); }
  .edge__red  { flex: 4; background: var(--brand-red); }
</style>
</head>
<body>

  <section class="card card--back" aria-label="Card back">
    <div class="wordmark"><span class="wordmark__dot"></span>RIDGELINE FINANCING</div>
    <p class="programs">
      $250,000 Application only Program<span class="programs__sep"></span>$250,000 Application only Program<br>
      Competitive Interest Rates<span class="programs__sep"></span>100% Financing
    </p>
  </section>

  <section class="card card--front" aria-label="Card front">
    <div class="holder">
      <p class="holder__name">DANIEL MARSH</p>
      <p class="holder__role">Graphic Designer</p>
    </div>

    <div class="wordmark"><span class="wordmark__dot"></span>RIDGELINE FINANCING</div>

    <p class="address">4417 W Canyon Mesa<br>Rd. STE B-2 #208 Mesa<br>AZ 85201</p>

    <ul class="contact">
      <li><svg viewBox="0 0 24 24" aria-hidden="true"><path d="M6.6 10.8a15.1 15.1 0 0 0 6.6 6.6l2.2-2.2c.3-.3.7-.4 1-.2 1.1.4 2.3.6 3.6.6.6 0 1 .4 1 1V20c0 .6-.4 1-1 1A17 17 0 0 1 3 4c0-.6.4-1 1-1h3.5c.6 0 1 .4 1 1 0 1.3.2 2.5.6 3.6.1.3 0 .7-.2 1z"/></svg>012 555 0148</li>
      <li><svg viewBox="0 0 24 24" aria-hidden="true"><path d="M2 5h20v14H2zm2 2v.5l8 5 8-5V7l-8 5z"/></svg>daniel@ridgelinefinance.com</li>
      <li><svg viewBox="0 0 24 24" aria-hidden="true"><path d="M12 2a10 10 0 1 0 0 20 10 10 0 0 0 0-20zm6.9 6h-3a15 15 0 0 0-1.3-3.9A8 8 0 0 1 18.9 8zM12 4c.9 1.2 1.5 2.6 1.9 4h-3.8c.4-1.4 1-2.8 1.9-4zM4.3 14a8 8 0 0 1 0-4h3.4a16 16 0 0 0 0 4zm.8 2h3a15 15 0 0 0 1.3 3.9A8 8 0 0 1 5.1 16zm3-8h-3a8 8 0 0 1 4.3-3.9C8.8 5.3 8.4 6.6 8.1 8zM12 20c-.9-1.2-1.5-2.6-1.9-4h3.8c-.4 1.4-1 2.8-1.9 4zm2.3-6H9.7a14 14 0 0 1 0-4h4.6a14 14 0 0 1 0 4zm.3 5.9c.6-1.2 1-2.5 1.3-3.9h3a8 8 0 0 1-4.3 3.9zm1.7-5.9a16 16 0 0 0 0-4h3.4a8 8 0 0 1 0 4z"/></svg>www.ridgelinefinance.com</li>
    </ul>

    <div class="edge"><span class="edge__blue"></span><span class="edge__red"></span></div>
  </section>

</body>
</html>
```